I need an 11 x 17 color poster to advertise a two week summer class I'm offering in video production through the Linden Hall Academy Summer Program. The classes are for middle school and high school students, so the poster should appeal to a young and creative crowd, but also look professional to their sophisticated parents. Posters will be placed on bulletin boards in book stores, coffee shops, school lobbies, etc, so they need to be eye-catching. Neon colors and bold graphic designs are encouraged. Perhaps stylized movie cameras and lights. I'd like to include a QR code and tear away tabs at the bottom with the registration URL on them.
Attached LHA Summer Program logo, should appear small next to the registration URL.
Include all of the following text:
Video Production Summer Crash Course
Get hands-on experience with:
-filming
-editing
-motion graphics
-stop motion animation
-green screen special effects
-and more!
Course taught by award-winning filmmaker and video artist Reid Calloway through the Linden Hall Academy Summer Program.
2-Week Sessions:
Middle School: 6/29-7/9 ($205)
High School: 7/27-8/6 ($225)
Details and registration: lindenhallnw.org/academics/summer_program
Target Market(s)
Creative middle and high school students and their parents.
Industry/Entity Type
Video Production
Look and feel

```html
<!DOCTYPE html>
<html lang="en">
<head>
<meta charset="utf-8">
<title>Video Production Summer Crash Course</title>
<link rel="stylesheet" href="https://fonts.googleapis.com/css2?family=Righteous&family=Schoolbell&family=Montserrat:wght@800&family=Oswald:wght@300;400&display=block">
<style>
  :root {
    --ink: #000000;
    --night: #03070f;
    --stage-blue: #1d5fa8;
    --stage-deep: #071a36;
    --glow: #8fd3ff;
    --neon-yellow: #fff200;
    --white: #ffffff;
    --strip-light: #3f7fc0;
    --strip-dark: #0b1f3a;
    --lens-dark: #0c0d12;
    --mark-blue: #2b4f8c;
  }
  * { margin: 0; padding: 0; box-sizing: border-box; }
  html, body { width: 776px; height: 1200px; overflow: hidden; background: var(--ink); }
  .poster {
    position: relative; width: 776px; height: 1200px; overflow: hidden;
    background: var(--night); color: var(--white); text-align: center;
  }

  .film-band { position: absolute; left: 0; width: 776px; }
  .film-band--top {
    top: 0; height: 62px;
    background: linear-gradient(180deg, var(--strip-dark) 0%, var(--strip-light) 50%, var(--strip-dark) 100%);
  }
  .film-band--middle {
    top: 586px; height: 70px;
    background: linear-gradient(180deg, var(--strip-dark) 0%, var(--strip-light) 50%, var(--strip-dark) 100%);
  }

  .stage {
    position: absolute; top: 62px; left: 0; width: 776px; height: 524px;
    background:
      radial-gradient(ellipse 260px 330px at 160px 40px, rgba(110,180,255,.55), transparent 70%),
      radial-gradient(ellipse 260px 330px at 620px 40px, rgba(110,180,255,.55), transparent 70%),
      linear-gradient(180deg, var(--stage-blue) 0%, var(--stage-deep) 45%, var(--ink) 80%);
  }
  .stage__floor-glow {
    position: absolute; left: 50px; top: 468px; width: 676px; height: 40px; border-radius: 50%;
    background: radial-gradient(ellipse at center, var(--white) 0%, var(--glow) 25%, rgba(30,110,200,.5) 55%, transparent 75%);
  }

  .title {
    position: absolute; top: 192px; left: 0; width: 100%;
    font-family: "Righteous", sans-serif; font-weight: 400;
    font-size: 58px; line-height: 64px; color: var(--neon-yellow); letter-spacing: 1px;
  }
  .instructor {
    position: absolute; top: 410px; left: 0; width: 100%;
    font-family: "Schoolbell", cursive; font-size: 23px; line-height: 42px;
  }
  .instructor__name { color: var(--neon-yellow); font-size: 30px; }

  .lens-photo {
    position: absolute; top: 656px; left: 0; width: 776px; height: 544px;
    background:
      radial-gradient(circle at 470px 340px, rgba(200,110,40,.55) 0%, rgba(90,50,25,.45) 14%, transparent 32%),
      radial-gradient(circle at 430px 320px, #1b1c25 0%, #15161d 40%, transparent 62%),
      radial-gradient(circle at 420px 300px, #2a2b33 0%, var(--lens-dark) 70%);
  }

  .details { position: absolute; top: 694px; left: 0; width: 100%; }
  .details__heading {
    font-family: "Montserrat", sans-serif; font-weight: 800; font-size: 27px; color: var(--neon-yellow);
  }
  .skills {
    margin-top: 8px; list-style: none;
    font-family: "Oswald", sans-serif; font-weight: 300; font-size: 25px; line-height: 37px;
  }
  .skills li { display: inline; }
  .skills li::before { content: "\2022"; margin-right: 4px; }

  .sessions { position: absolute; top: 868px; left: 0; width: 100%; }
  .label { font-family: "Schoolbell", cursive; font-size: 20px; color: var(--neon-yellow); font-weight: 400; }
  .sessions__list {
    list-style: none; font-family: "Oswald", sans-serif; font-weight: 300; font-size: 18px; line-height: 27px;
  }

  .registration { position: absolute; top: 1012px; left: 0; width: 100%; }
  .registration .label { font-size: 22px; line-height: 30px; }
  .registration__url { font-family: "Oswald", sans-serif; font-weight: 300; font-size: 19px; line-height: 30px; }

  .program-mark {
    position: absolute; top: 1100px; left: 338px; width: 116px; height: 80px;
    background: var(--white); display: flex; align-items: center; justify-content: center; padding: 6px;
    font-family: "Oswald", sans-serif; font-weight: 400; font-size: 12px; line-height: 14px; color: var(--mark-blue);
  }
</style>
</head>
<body>
<main class="poster">
  <div class="film-band film-band--top" role="img" aria-label="Film strip band with sprocket holes"></div>

  <div class="stage" role="img" aria-label="Blue theatre stage with spotlights and twinkling stars">
    <div class="stage__floor-glow"></div>
  </div>

  <h1 class="title">Video Production<br>Summer Crash Course</h1>

  <p class="instructor">Course taught by award-winning filmmaker<br>
    and video artist <span class="instructor__name">Reid Calloway</span><br>
    through the Linden Hall Academy Summer Program.</p>

  <div class="film-band film-band--middle" role="img" aria-label="Film strip band with sprocket holes"></div>

  <div class="lens-photo" role="img" aria-label="Close-up of a camera lens glowing amber in the dark"></div>

  <section class="details">
    <h2 class="details__heading">GET HANDS-ON EXPERIENCE WITH:</h2>
    <ul class="skills">
      <li>filming</li> <li>editing</li> <li>motion graphics</li> <li>stop motion animation</li><br>
      <li>green screen special effects</li> <li>and more!</li>
    </ul>
  </section>

  <section class="sessions">
    <h3 class="label">2-Week Sessions:</h3>
    <ul class="sessions__list">
      <li>Middle School: 6/29-7/9 ($205)</li>
      <li>High School: 7/27-8/6 ($225)</li>
    </ul>
  </section>

  <section class="registration">
    <h3 class="label">Details and registration:</h3>
    <p class="registration__url">lindenhallnw.org/academics/summer_program</p>
  </section>

  <div class="program-mark">Linden Hall Academy Summer Program</div>
</main>
</body>
</html>
```